“Professional 9x12 Pocket Folder Design – Roofing, Siding, Windows, Doors, Decks, Solar

✅ Page 1: Front Cover (Main Visual Impact)

Goal: Strong visual first impression representing all services Kelby’s Roofing offers.

Design Instructions:
• Top: Big, bold headline with Kelby’s Roofing (or company logo).
• Center: A high-quality image of a beautiful home that clearly shows:
• New roof (preferably dark shingles)
• Modern black-trim windows
• Upgraded front door
• Stylish siding (horizontal or board & batten)
• Visible garage door
• Optional: solar panels on the roof
• Optional: small composite front porch or deck
• Bottom Section (beneath the house image): Add keywords like:
Roofing • Siding • Windows • Doors • Decks • Solar • Local & Trusted

⸻

✅ Page 2: Back Cover

Goal: Tell the story of the company + display contact information for offices.

Design Instructions:
• Top Half: Section titled:
Our Story or About Kelby’s Roofing

Suggested Text (can be customized):
With over two decades of dedication to quality craftsmanship, Kelby’s Roofing has grown from a small local team into one of the region’s most trusted names in exterior home improvement. Our mission is to bring lasting beauty, energy efficiency, and protection to every home we touch.
• Bottom Half: Title:
Our Offices

Include up to 4 office addresses

Kelby's Roofing
2817 Tamarind St.
Ashcombe, MA 02419
Kelby's Roofing
3390 Fenlow Ave, Warwick, RI 02715
Kelby's Roofing
716 N Ashdale St, Middleborough, MA 02193
Kelby's Roofing
4129 Pelland Hwy, East Wareham, MA 02467 ( Showroom )

⸻

✅ Inside Pockets

🔹 Left Pocket:

Title:

We’d Love Your Feedback

Text Suggestion:

Enjoyed your experience? Please leave us a review. Your feedback helps us grow and serve others better.

Add a QR code linking to the review page.for rateloop reviews

🔹 Right Pocket:

Your Product Specialist
Tobin Vasquel
📞 B:781-555-0142
P:774-555-0187
✉️ tvasquel@kelbyroofco.example

Let this info be printed/stamped directly on the folder, not using business cards
Our website https://kelbyroofco.example/?sfw=pass1751118580#

Feel free to take pictures from the website and use anything that is needed .

If we can add a flyer extra I’ll be willing to pay for that separate .
✅ Flyer Insert #1 (Double-Sided)

🔹 SIDE A: “Before & After Showcase”
• 4 Sections (lined up cleanly):
• Roofing
• Windows
• Skylights
• Decks
Each section includes:
• 📸 Before / After photo
• ✍️ Small description of the job (town + result)

🔹 SIDE B: “The Project Journey”

“What to Expect When You Work with Tobin”

• Step 1: Free Home Visit & Consultation
• Step 2: Custom Design Solutions
• Step 3: Quality Installation by Experts
• Step 4: Final Walkthrough + Satisfaction Check
• Soft closing line

Please use our best before and after pictures and take the data from Kelbyroofco.example

```html
<!DOCTYPE html>
<html lang="en">
<head>
<meta charset="utf-8">
<title>Kelby’s Roofing – Flyer Insert</title>
<link rel="stylesheet" href="https://fonts.googleapis.com/css2?family=Tinos:wght@400;700&family=Montserrat:wght@500;600;800&display=swap">
<style>
:root{
  --navy:#28307f;
  --navy-deep:#1c2260;
  --gold:#d4c08a;
  --gold-dark:#b9a266;
  --ink:#1a1a1a;
  --paper:#ffffff;
  --bg:#f4f4f4;
}
*{box-sizing:border-box;margin:0;padding:0}
html,body{width:1200px;height:966px;overflow:hidden;background:var(--bg)}
body{position:relative;font-family:"Tinos",serif;color:var(--ink)}
.page{position:absolute;top:122px;width:514px;height:665px;background:var(--paper);overflow:hidden;box-shadow:0 6px 18px rgba(0,0,0,.18)}
.page--front{left:71px}
.page--back{left:627px}
.header-band{position:absolute;left:0;top:0;width:514px}
.brand{position:absolute;left:50%;transform:translateX(-50%);background:var(--paper);border:2px solid var(--navy);width:176px;height:56px;display:flex;align-items:center;justify-content:center}
.brand__name{font-family:"Tinos",serif;font-weight:700;font-size:20px;color:var(--navy);line-height:1;white-space:nowrap}
.brand__dot{display:inline-block;width:8px;height:8px;background:var(--gold);border-radius:50%;margin-right:6px;vertical-align:3px}
.page--front .brand{top:46px}
.page--back .brand{top:174px}

/* showcase rows */
.showcase{position:absolute;left:42px;width:439px;height:102px;display:flex;border-radius:12px;overflow:hidden;background:var(--paper)}
.photo{position:relative;width:127px;height:100%;flex:none}
.photo--before{background:linear-gradient(160deg,#6f8fb8 0%,#8a9a7a 45%,#c9c2b0 70%,#5f6f4a 100%)}
.photo--after{background:linear-gradient(160deg,#7d95b5 0%,#5c6b6a 45%,#3c4249 70%,#4d5f3e 100%)}
.tag{position:absolute;top:4px;font-weight:700;font-size:11px;padding:2px 9px}
.tag--before{left:4px;background:var(--gold);color:var(--ink);border-radius:6px 0 6px 0}
.tag--after{right:3px;background:var(--navy);color:#fff;border-radius:8px 0 0 8px}
.service{position:relative;width:185px;flex:none;border-top:3px solid var(--gold);text-align:center}
.service__title{display:inline-block;background:var(--gold);font-weight:700;font-size:14px;letter-spacing:.5px;padding:1px 16px 3px;border-radius:0 0 12px 12px;margin-bottom:5px}
.service__text{font-size:6.8px;line-height:1.24;padding:0 11px}

.cta{position:absolute;left:42px;width:430px;height:33px;background:var(--navy);border-radius:17px;color:#fff;font-weight:700;font-size:17px;text-align:center;line-height:31px;border-bottom:2px solid var(--gold);white-space:nowrap}
.contact{position:absolute;left:0;width:514px;top:626px;display:flex;justify-content:space-around;padding:0 40px;font-family:"Montserrat",sans-serif;font-weight:600;font-size:11.2px;white-space:nowrap}

/* back page */
.journey-title{position:absolute;top:28px;left:0;width:514px;text-align:center;font-weight:700;font-size:108px;line-height:1;color:#fff;letter-spacing:-1px}
.journey-kicker{position:absolute;top:44px;left:0;width:514px;padding-left:32px;text-align:center;font-weight:700;font-size:26px;letter-spacing:5px;color:var(--gold);line-height:1}
.steps{position:absolute;top:274px;left:0;width:514px}
.step{position:absolute;width:120px;margin-left:-60px;text-align:center}
.step__label{font-weight:700;font-size:20px;color:var(--navy)}
.step__badge{width:78px;height:78px;margin:4px auto 0;border-radius:50%;background:var(--gold);border:4px solid var(--navy)}
.step__caption{margin-top:16px;font-weight:700;font-size:10px;line-height:1;color:var(--navy)}
.step-arrow{position:absolute;top:308px}
.promise{position:absolute;left:44px;width:426px;top:443px;border-top:1px solid var(--gold);border-bottom:1px solid var(--gold);text-align:center;font-weight:700;font-size:19px;padding:3px 0 4px;white-space:nowrap}
.promise-text{position:absolute;left:44px;width:426px;top:484px;font-family:"Montserrat",sans-serif;font-weight:500;font-size:9.6px;line-height:1.3;text-align:center}
.estimate{position:absolute;left:0;width:514px;top:594px;text-align:center;font-family:"Montserrat",sans-serif;font-weight:800;font-size:16.5px;letter-spacing:.2px;white-space:nowrap}
.estimate__star{color:var(--gold);font-size:13px;letter-spacing:2px;margin:0 6px}
</style>
</head>
<body>

<section class="page page--front">
  <svg class="header-band" width="514" height="110" viewBox="0 0 514 110">
    <defs>
      <linearGradient id="hdrFront" x1="0" y1="0" x2="1" y2="1">
        <stop offset="0" stop-color="#2a3377"/><stop offset="1" stop-color="#1c2260"/>
      </linearGradient>
    </defs>
    <polygon points="0,0 514,0 514,54 257,96 0,54" fill="url(#hdrFront)" role="img" aria-label="Photo of the company office and parking lot, tinted navy"/>
    <polygon points="0,54 257,96 514,54 514,62 257,104 0,62" fill="var(--gold)"/>
  </svg>
  <div class="brand"><div class="brand__name"><span class="brand__dot"></span>Kelby’s Roofing</div></div>

  <div class="showcase" style="top:138px">
    <div class="photo photo--before" role="img" aria-label="Before: colonial house with worn roof"><span class="tag tag--before">Before</span></div>
    <div class="service"><span class="service__title">ROOFING</span>
      <p class="service__text">We offer a wide range of roofing services throughout the area. From replacements to repairs &amp; maintenance work, we have the years of experience and the high-quality materials needed to tackle projects of any size. Our team can evaluate the condition of your roof and offer a variety of suggestions for maintenance, repair or replacement.</p></div>
    <div class="photo photo--after" role="img" aria-label="After: colonial house with new dark roof"><span class="tag tag--after">After</span></div>
  </div>

  <div class="showcase" style="top:247px">
    <div class="photo photo--before" role="img" aria-label="Before: brick wall with window opening removed"><span class="tag tag--before">Before</span></div>
    <div class="service"><span class="service__title">WINDOWS</span>
      <p class="service__text">Our leading contractors provide and professionally install high quality windows &amp; sliders. Replacement windows dramatically reduce your energy bills while increasing the value of your home. From vinyl windows to beautiful bay windows we have the available resources and skilled contractors to get you results.</p></div>
    <div class="photo photo--after" role="img" aria-label="After: new bay window in brick wall"><span class="tag tag--after">After</span></div>
  </div>

  <div class="showcase" style="top:356px">
    <div class="photo photo--before" role="img" aria-label="Before: house with sunroom under construction"><span class="tag tag--before">Before</span></div>
    <div class="service"><span class="service__title">SKYLIGHTS</span>
      <p class="service__text">Kelby’s Roofing is proud to be a certified installer of Lumaris skylights. For over sixty years, Lumaris has been a leader in skylight and roof light solutions. They are highly focused in having the best quality and most energy-efficient daylighting products. Since we have been in business, we are one of Lumaris’s leading installers in the area.</p></div>
    <div class="photo photo--after" role="img" aria-label="After: finished sunroom with skylights"><span class="tag tag--after">After</span></div>
  </div>

  <div class="showcase" style="top:465px">
    <div class="photo photo--before" role="img" aria-label="Before: grey house with old entry stairs"><span class="tag tag--before">Before</span></div>
    <div class="service"><span class="service__title">DECKS</span>
      <p class="service__text">Kelby’s is proud to offer decking replacement, and installation to homeowners in Ashcombe, MA, and its surrounding area. When you hire our team for your decking project, you can expect outstanding results that are sure to last you years and years. As is the case with all of our services, we work strictly with industry-leading and trusted manufacturers in our decking projects.</p></div>
    <div class="photo photo--after" role="img" aria-label="After: blue house with new white entry deck"><span class="tag tag--after">After</span></div>
  </div>

  <div class="cta" style="top:582px">Let's Work Together to Create the Home You Deserve</div>
  <div class="contact"><span>www.kelbyroofco.example</span><span>781.555.0199</span><span>info@kelbyroofco.example</span></div>
</section>

<section class="page page--back">
  <svg class="header-band" width="514" height="200" viewBox="0 0 514 200">
    <defs>
      <linearGradient id="hdrBack" x1="0" y1="0" x2="1" y2="1">
        <stop offset="0" stop-color="#2a3377"/><stop offset="1" stop-color="#1c2260"/>
      </linearGradient>
    </defs>
    <polygon points="0,0 514,0 514,146 257,184 0,146" fill="url(#hdrBack)" role="img" aria-label="Photo of the company office and parking lot, tinted navy"/>
    <polygon points="0,146 257,184 514,146 514,154 257,192 0,154" fill="var(--gold)"/>
  </svg>
  <div class="journey-title">Journey</div>
  <div class="journey-kicker">THE PROJECT</div>
  <div class="brand"><div class="brand__name"><span class="brand__dot"></span>Kelby’s Roofing</div></div>

  <div class="steps">
    <div class="step" style="left:86px"><div class="step__label">Step 1</div><div class="step__badge" role="img" aria-label="Icon: contractor visiting a home"></div><div class="step__caption">Free Home<br>Visit &amp;<br>Consultation</div></div>
    <div class="step" style="left:197px"><div class="step__label">Step 2</div><div class="step__badge" role="img" aria-label="Icon: design plans and pencil"></div><div class="step__caption">Custom<br>Design<br>Solutions</div></div>
    <div class="step" style="left:309px"><div class="step__label">Step 3</div><div class="step__badge" role="img" aria-label="Icon: thumbs up with stars"></div><div class="step__caption">Quality<br>Installation<br>by Experts</div></div>
    <div class="step" style="left:423px"><div class="step__label">Step 4</div><div class="step__badge" role="img" aria-label="Icon: walking out through a door"></div><div class="step__caption">Final<br>Walkthrough +<br>Satisfaction Check</div></div>
  </div>
  <svg class="step-arrow" style="left:118px" width="40" height="46" viewBox="0 0 40 46"><path d="M4 44 C22 40 22 14 32 10 L38 10" fill="none" stroke="var(--gold)" stroke-width="2"/><path d="M33 6 L39 10 L33 14" fill="var(--gold)"/></svg>
  <svg class="step-arrow" style="left:229px" width="40" height="46" viewBox="0 0 40 46"><path d="M4 44 C22 40 22 14 32 10 L38 10" fill="none" stroke="var(--gold)" stroke-width="2"/><path d="M33 6 L39 10 L33 14" fill="var(--gold)"/></svg>
  <svg class="step-arrow" style="left:341px" width="40" height="46" viewBox="0 0 40 46"><path d="M4 44 C22 40 22 14 32 10 L38 10" fill="none" stroke="var(--gold)" stroke-width="2"/><path d="M33 6 L39 10 L33 14" fill="var(--gold)"/></svg>

  <div class="promise">We Won't Soak You To Keep You Warm and Dry</div>
  <p class="promise-text">We pride ourselves in providing superlative workmanship at competitive prices and treating our clients’ homes like our own. The customers experience from start to finish is the most important thing for us. That is why providing the workmanship, customer service and a good price helps to go a long way.</p>

  <div class="cta" style="top:546px">Let's Work Together to Create the Home You Deserve</div>
  <div class="estimate"><span class="estimate__star">★★</span>GIVE US A CALL FOR A FREE ESTIMATE<span class="estimate__star">★★</span></div>
  <div class="contact"><span>www.kelbyroofco.example</span><span>781.555.0199</span><span>info@kelbyroofco.example</span></div>
</section>

</body>
</html>
```